Auto Body Shops Needs Email Signature Design

We are looking to update our email signature. The design needs to be easy to copy and paste into Microsoft Outlook and be editable for multiple positions.

Our company is called Dellwyn Collision & Autoglass, but we have a charity program called Dellwyn Helps Young Ones. We would like to use this logo.

Information that needs to be included:

"We Care"
Name
Title
Location
Address
Phone
Email
Cell
Fax

Our new corporate colors are gray/silver and black. We are getting away from blue (currently used).

The "Dellwyn" and "Helps Young" should be in black as they will be on a white background (comp screen).

Colors
fde1e1

Requirements
Must have
• Easily editable so it can be used as a template.
Should not have
• Main color should not be red.

```html
<!DOCTYPE html>
<html lang="en">
<head>
<meta charset="utf-8">
<title>Dellwyn Email Signature</title>
<link href="https://fonts.googleapis.com/css2?family=Carlito:wght@400;700&family=Roboto+Slab:wght@300;400;700&family=Open+Sans:wght@400;600&display=swap" rel="stylesheet">
<style>
  :root {
    --titlebar: #1f6fc4;
    --titlebar-text: #ffffff;
    --ribbon: #f3f3f3;
    --ribbon-line: #d4d4d4;
    --ribbon-text: #333333;
    --group-label: #666666;
    --pane: #ffffff;
    --band: #ececec;
    --selected: #dcdcdc;
    --list-blue: #1a62b8;
    --page: #ffffff;
    --ink: #111111;
    --body-text: #1a1a1a;
    --muted: #555555;
    --header-text: #555555;
    --accent-red: #e8262c;
    --link-blue: #1a0dff;
    --link-red: #c0211f;
    --tint: #fde1e1;
    --status: #f0f0f0;
    --scroll: #c8c8c8;
  }
  html, body {
    margin: 0; padding: 0;
    width: 1200px; height: 779px;
    overflow: hidden;
    background: var(--page);
  }
  .window {
    position: relative;
    width: 1200px; height: 779px;
    font-family: "Open Sans", "Segoe UI", sans-serif;
    color: var(--ribbon-text);
  }
  .abs { position: absolute; white-space: nowrap; }

  /* title bar */
  .titlebar {
    position: absolute; left: 0; top: 0; width: 1200px; height: 31px;
    background: var(--titlebar); color: var(--titlebar-text); font-size: 14px;
  }
  .titlebar .abs { top: 6px; }

  /* ribbon */
  .ribbon {
    position: absolute; left: 0; top: 31px; width: 1200px; height: 103px;
    background: var(--ribbon); border-bottom: 1px solid var(--ribbon-line);
    font-size: 13.5px;
  }
  .ribbon-group-label { position: absolute; top: 85px; font-size: 12.5px; color: var(--group-label); }
  .ribbon-sep { position: absolute; top: 6px; width: 1px; height: 92px; background: var(--ribbon-line); }
  .ribbon-btn { position: absolute; text-align: center; font-size: 13.5px; line-height: 17px; }
  .ribbon-btn svg { display: block; margin: 0 auto 3px; }
  .ribbon-small { position: absolute; display: flex; align-items: center; gap: 5px; font-size: 13.5px; }
  .quick-steps {
    position: absolute; left: 229px; top: 5px; width: 285px; height: 70px;
    background: #ffffff; border: 1px solid var(--ribbon-line);
  }
  .search-box {
    position: absolute; left: 869px; top: 4px; width: 111px; height: 22px;
    border: 1px solid var(--ribbon-line); background: #fff; font-size: 13px;
    color: #666; padding: 2px 4px; box-sizing: border-box;
  }

  /* folder list */
  .folder-pane {
    position: absolute; left: 0; top: 135px; width: 78px; height: 620px;
    background: var(--pane); border-right: 1px solid var(--ribbon-line);
    font-size: 12.5px;
  }
  .folder-select {
    position: absolute; left: -2px; top: 9px; width: 66px; height: 20px;
    border: 1px solid var(--ribbon-line); box-sizing: border-box; color: #666; padding-left: 2px;
  }
  .list-band { position: absolute; left: 0; width: 45px; background: var(--band); }
  .list-time { position: absolute; left: 0; font-weight: 600; color: #333; }
  .list-time.unread { color: var(--list-blue); }
  .list-scroll { position: absolute; left: 53px; top: 40px; width: 17px; height: 578px; border: 1px solid var(--ribbon-line); box-sizing: border-box; background: #fafafa; }

  /* message header */
  .message-actions { position: absolute; left: 97px; top: 148px; display: flex; gap: 14px; font-size: 13.5px; }
  .message-actions span { display: inline-flex; align-items: center; gap: 4px; }
  .avatar { position: absolute; left: 92px; top: 175px; width: 53px; height: 53px; background: #c6c6c6; }
  .sender { position: absolute; left: 167px; top: 176px; font-size: 15.5px; color: var(--header-text); }
  .recipients { position: absolute; left: 503px; top: 180px; font-size: 12px; color: var(--header-text); }
  .header-rule { position: absolute; left: 92px; top: 244px; width: 1099px; height: 1px; background: var(--ribbon-line); }

  /* message body */
  .message {
    position: absolute; left: 104px; top: 260px; width: 1050px;
    font-family: "Carlito", "Calibri", sans-serif;
    color: var(--body-text);
  }
  .message-text { font-size: 17.8px; line-height: 23.2px; margin: 0 0 23px; }
  .tagline { font-family: "Roboto Slab", serif; font-weight: 700; font-size: 17.5px; color: var(--accent-red); margin: 0 0 43px; }
  .person-name { font-family: "Roboto Slab", serif; font-weight: 700; font-size: 23px; color: #2a2a2a; margin: 0 0 12px; }
  .person-role { font-family: "Roboto Slab", serif; font-weight: 300; font-size: 17.5px; color: var(--muted); margin: 0 0 11px; }
  .person-role a { color: var(--link-blue); }
  .contact-line { display: flex; align-items: center; gap: 2px; font-family: "Roboto Slab", serif; font-weight: 300; font-size: 17.5px; color: var(--ink); margin: 0 0 6px; }
  .contact-item { display: inline-flex; align-items: center; gap: 3px; margin-right: 3px; }
  .brand-mark { display: flex; align-items: center; gap: 8px; margin: 0 0 10px 10px; height: 40px; font-family: "Roboto Slab", serif; font-weight: 700; font-size: 20px; color: var(--ink); }
  .brand-dot { width: 14px; height: 14px; border-radius: 50%; background: var(--accent-red); }
  .site-link { display: block; margin-left: 8px; font-family: "Roboto Slab", serif; font-weight: 300; font-size: 16.5px; color: var(--link-red); }

  .body-scroll { position: absolute; left: 1173px; top: 263px; width: 18px; height: 480px; border: 1px solid var(--ribbon-line); box-sizing: border-box; background: #fafafa; }
  .scroll-thumb { position: absolute; left: 2px; width: 12px; background: #fff; border: 1px solid var(--scroll); }

  /* status bar */
  .statusbar { position: absolute; left: 0; top: 756px; width: 1200px; height: 23px; background: var(--status); border-top: 1px solid var(--ribbon-line); font-size: 12.5px; color: #333; }
  .statusbar .abs { top: 4px; }
</style>
</head>
<body>
<div class="window">

  <header class="titlebar">
    <span class="abs" style="left:20px">View</span>
    <span class="abs" style="left:80px">Shield</span>
    <span class="abs" style="left:139px">&#x1F4A1;&#xFE0E; Tell me what you want to do</span>
  </header>

  <nav class="ribbon">
    <div class="ribbon-btn" style="left:-6px;top:6px">
      <svg width="30" height="30" viewBox="0 0 30 30"><path d="M4 12 L15 4 L26 12 V26 H4 Z" fill="#fff" stroke="#777"/><path d="M2 20 h10 M2 20 l4 -4 M2 20 l4 4" stroke="#8a5bd1" stroke-width="2" fill="none"/></svg>Reply</div>
    <div class="ribbon-btn" style="left:42px;top:6px">
      <svg width="30" height="30" viewBox="0 0 30 30"><path d="M4 12 L15 4 L26 12 V26 H4 Z" fill="#fff" stroke="#777"/><path d="M6 20 h12 M6 20 l4 -4 M6 20 l4 4" stroke="#8a5bd1" stroke-width="2" fill="none"/></svg>Reply<br>All</div>
    <div class="ribbon-btn" style="left:85px;top:6px">
      <svg width="30" height="30" viewBox="0 0 30 30"><path d="M4 12 L15 4 L26 12 V26 H4 Z" fill="#fff" stroke="#777"/><path d="M14 20 h12 M26 20 l-4 -4 M26 20 l-4 4" stroke="#1f6fc4" stroke-width="2" fill="none"/></svg>Forward</div>
    <div class="ribbon-small" style="left:140px;top:14px"><svg width="14" height="14"><rect x="1" y="2" width="12" height="11" fill="#fff" stroke="#555"/><rect x="1" y="2" width="12" height="3" fill="#555"/></svg>Meeting</div>
    <div class="ribbon-small" style="left:140px;top:41px"><svg width="14" height="14"><rect x="1" y="1" width="12" height="12" fill="#fff" stroke="#555"/><path d="M4 5h6M4 8h6" stroke="#1f6fc4"/></svg>More &#9662;</div>
    <span class="ribbon-group-label" style="left:78px">Respond</span>
    <div class="ribbon-sep" style="left:224px"></div>

    <div class="quick-steps">
      <div class="ribbon-small" style="left:4px;top:4px"><svg width="16" height="14"><rect x="1" y="3" width="14" height="10" fill="#e8b44a"/></svg>Move to: ?</div>
      <div class="ribbon-small" style="left:4px;top:26px"><svg width="16" height="14"><rect x="1" y="2" width="14" height="10" fill="#fff" stroke="#555"/></svg>Team Email</div>
      <div class="ribbon-small" style="left:4px;top:48px"><svg width="16" height="14"><rect x="1" y="2" width="14" height="10" fill="#fff" stroke="#555"/></svg>Reply &amp; Delete</div>
      <div class="ribbon-small" style="left:138px;top:4px"><svg width="16" height="14"><rect x="1" y="2" width="14" height="10" fill="#fff" stroke="#555"/><path d="M9 10h5" stroke="#1f6fc4" stroke-width="2"/></svg>To Manager</div>
      <div class="ribbon-small" style="left:138px;top:26px"><svg width="16" height="14"><path d="M2 7 L6 12 L14 2" stroke="#444" stroke-width="2" fill="none"/></svg>Done</div>
      <div class="ribbon-small" style="left:138px;top:48px"><svg width="16" height="14"><path d="M8 1 L3 8 H8 L6 13 L13 5 H8 Z" fill="#e8b44a"/></svg>Create New</div>
      <div style="position:absolute;right:0;top:0;width:12px;height:70px;border-left:1px solid var(--ribbon-line)"></div>
    </div>
    <span class="ribbon-group-label" style="left:331px">Quick Steps</span>
    <div class="ribbon-sep" style="left:521px"></div>

    <div class="ribbon-btn" style="left:533px;top:6px"><svg width="34" height="30"><rect x="2" y="6" width="30" height="22" fill="#e8b44a"/><path d="M6 4 h8" stroke="#1f6fc4" stroke-width="3"/></svg>Move<br>&#9662;</div>
    <div class="ribbon-btn" style="left:583px;top:6px"><svg width="34" height="30"><rect x="2" y="6" width="30" height="22" fill="#e8b44a"/><rect x="12" y="14" width="16" height="10" fill="#fff" stroke="#555"/></svg>Rules<br>&#9662;</div>
    <div class="ribbon-btn" style="left:624px;top:6px"><svg width="34" height="30"><rect x="6" y="3" width="22" height="24" fill="#bbb"/></svg>Notes</div>
    <span class="ribbon-group-label" style="left:587px">Move</span>
    <div class="ribbon-sep" style="left:686px"></div>

    <div class="ribbon-btn" style="left:693px;top:6px"><svg width="34" height="30"><path d="M4 12 L17 4 L30 12 V27 H4 Z" fill="#fff" stroke="#777"/></svg>Unread/<br>Read</div>
    <div class="ribbon-btn" style="left:746px;top:6px"><svg width="34" height="30"><rect x="5" y="3" width="11" height="11" fill="#e2683c"/><rect x="18" y="3" width="11" height="11" fill="#5b9bd5"/><rect x="5" y="16" width="11" height="11" fill="#70ad47"/><rect x="18" y="16" width="11" height="11" fill="#ffc000"/></svg>Categorize<br>&#9662;</div>
    <div class="ribbon-btn" style="left:815px;top:6px"><svg width="34" height="30"><path d="M9 28 V3" stroke="#666" stroke-width="2"/><path d="M10 3 H26 L22 9 L26 15 H10 Z" fill="#e2483c"/></svg>Follow<br>Up &#9662;</div>
    <span class="ribbon-group-label" style="left:762px">Tags</span>
    <div class="ribbon-sep" style="left:866px"></div>

    <div class="search-box">Search People</div>
    <div class="ribbon-small" style="left:872px;top:31px"><svg width="16" height="14"><rect x="2" y="1" width="12" height="12" fill="#fff" stroke="#555"/><path d="M5 5h6M5 8h6" stroke="#555"/></svg>Address Book</div>
    <div class="ribbon-small" style="left:872px;top:55px"><svg width="16" height="14"><path d="M1 1 H15 L9 7 V13 L7 12 V7 Z" fill="#555"/></svg>Filter Email &#9662;</div>
    <span class="ribbon-group-label" style="left:911px">Find</span>
    <div class="ribbon-sep" style="left:987px"></div>

    <div class="ribbon-btn" style="left:998px;top:6px"><svg width="34" height="30"><rect x="5" y="5" width="24" height="24" fill="#e8462c"/></svg>Store</div>
    <span class="ribbon-group-label" style="left:992px">Add-ins</span>
  </nav>

  <aside class="folder-pane">
    <div class="folder-select">Mailbox &#9662;</div>
    <span class="abs" style="left:0;top:45px">west &#8595;</span>
    <div class="list-band" style="top:94px;height:69px;background:var(--selected)"></div>
    <span class="list-time" style="top:119px">:14</span>
    <span class="list-time" style="top:188px">:02</span>
    <span class="list-time" style="top:257px">:17</span>
    <div class="list-band" style="top:300px;height:25px"></div>
    <span class="list-time unread" style="top:353px">:41</span>
    <div class="list-band" style="top:397px;height:25px"></div>
    <span class="list-time unread" style="top:459px">:31</span>
    <div class="list-band" style="top:494px;height:25px"></div>
    <span class="list-time unread" style="top:546px">8.5</span>
    <div class="list-scroll"><div class="scroll-thumb" style="top:16px;height:18px"></div></div>
  </aside>

  <div class="message-actions">
    <span><svg width="16" height="14"><path d="M2 6 L8 1 L14 6 V13 H2 Z" fill="#fff" stroke="#777"/></svg>Reply</span>
    <span><svg width="16" height="14"><path d="M2 6 L8 1 L14 6 V13 H2 Z" fill="#fff" stroke="#777"/></svg>Reply All</span>
    <span><svg width="16" height="14"><path d="M2 6 L8 1 L14 6 V13 H2 Z" fill="#fff" stroke="#777"/></svg>Forward</span>
  </div>
  <div class="avatar" role="img" aria-label="Sender avatar placeholder"></div>
  <span class="sender">Mark Dalton &lt;mdalton@mailbox.net&gt;</span>
  <div class="abs" style="left:481px;top:176px;width:1px;height:22px;background:var(--ribbon-line)"></div>
  <span class="recipients">lena.petrova@mailhub.net; Mark Dalton &#9662;</span>
  <span class="abs" style="left:1160px;top:180px;font-size:12.5px;color:#555">21:13</span>
  <span class="abs" style="left:1178px;top:212px;font-size:14px;color:#555">&#8964;</span>
  <div class="header-rule"></div>

  <main class="message">
    <p class="message-text">Dear Sirs,</p>
    <p class="message-text">Iusto viris labitur ea per, te mei vitae soleat. Cu nec porro atomorum, aeterno antiopam mel cu, assum sonet epicurei mel ex. Nam ad prompta luptatum indoctum, et eum natum iuvaret. Possit blandit persecuti sed no. Pri porro quando praesent ad, delectus consequat nam te. Has eu nobis equidem disputationi.</p>
    <p class="message-text">Meis efficiantur ex duo, has eu mundi sententiae temporibus, ludus putant expetendis has ei. Nusquam fierent menandri pri ex, eu cum oblique scaevola repudiandae, graece adipisci persecuti in sea. Utinam ridens postulant eu mel. Ea eam mollis mentitum hendrerit. Ne reque ludus molestiae est, per iusto tamquam voluptatibus ex, ea has justo omnium.</p>

    <section class="signature">
      <p class="tagline">We Care</p>
      <p class="person-name">Your Name</p>
      <p class="person-role">Regional Manager | H.O. Brookfield | <a href="mailto:email@dellwyn.com">email@dellwyn.com</a></p>
      <p class="contact-line">
        <span class="contact-item">
          <svg width="18" height="18" viewBox="0 0 18 18" aria-hidden="true"><rect x="5" y="1" width="8" height="16" rx="1.5" fill="#e8262c"/><rect x="6.5" y="3" width="5" height="9" fill="#fde1e1"/></svg>604-555-0142
        </span>
        <span class="contact-item">
          <svg width="18" height="18" viewBox="0 0 18 18" aria-hidden="true"><rect x="4" y="1" width="10" height="6" fill="#fde1e1" stroke="#e8262c"/><rect x="1" y="6" width="16" height="9" rx="1.5" fill="#e8262c"/><rect x="4" y="10" width="10" height="2" fill="#fde1e1"/></svg>604-555-0142
        </span>
      </p>
      <div class="brand-mark"><span class="brand-dot"></span>Dellwyn Helps Young Ones</div>
      <a class="site-link" href="http://www.dellwyn.com/">http://www.dellwyn.com/</a>
    </section>
  </main>

  <div class="body-scroll"><div class="scroll-thumb" style="top:28px;height:340px"></div></div>

  <footer class="statusbar">
    <span class="abs" style="left:533px">All folders are up to date.</span>
    <span class="abs" style="left:700px">Connected to: Mail Server</span>
    <div class="abs" style="left:918px;top:0;width:42px;height:23px;background:#d6d6d6"></div>
    <span class="abs" style="left:1007px">&#8211;</span>
    <div class="abs" style="left:1020px;top:11px;width:116px;height:1px;background:#777"></div>
    <div class="abs" style="left:1074px;top:5px;width:4px;height:13px;background:#555"></div>
    <span class="abs" style="left:1136px">+</span>
    <span class="abs" style="left:1161px">116%</span>
  </footer>
</div>
</body>
</html>
```